Maple Lantern Productions web site

I need to build a website for a new company I am launching next month. Maple Lantern Productions is a company based in New England that provides sound, lighting, and audio visual services to weddings, corporate, and any other cusomer base looking for quality service for a fair price. Looking for somebody to do a full site not just the image files. I am looking to keep the colors of my logo (orange and black) and possibly grey and white. I am looking to build my site very similar to brightvaleevents.example, which is owned by a friend of mine. I like how he has the big pictures that load in to the site and the basic menu items. I'll need a gallery of photos. The designs should communicate quality, value and trust.
My website address is maplelanternco.example.
Updates

Hi and thanks to everyone for posting such great ideas for our new design.I have some items that I'd like to ask you all to focus on in your revisions.I like how http://www.brightvaleevents.example/ website has five or six high res pictures that change in a slideshow format with a caption that loads in for each one for the different types of services. Try and capture pics like these and with teh same headings as he has. The basic menu designs have been interesting.I am more fond of the menus that are more white with some orange as I dont want it to be too dark. I'm curious to see how your galleries will work and if i'll be able to edit the pages myself? I have some more info on the company for you to fill in:website address is ciderhouseco.comemail: info@ciderhouseco.comaddress: Maple Lantern Productions57 Littlefield StreetAvon, MA 02417"New England's finest DJ's, lighting and sound, video and more. Creating memories one perfect event at a time."Put this under the loading pictures as a tagline.About Cider HouseCider House Productions is a collection of New England's finest talent, ready to make your next event the one you've dreamed of. We have the skills and expertise to deliver your vision of your perfect event. From elegant weddings to themed mitzvah's, corporate av, videography and detail lighting, we offer all of the elements to make your event a success. Added Wednesday, March 1, 2017

Designer's Please also make sure that your design flows well on any device it is being viewed on as well. Thanks. Added Wednesday, March 1, 2017

Project Deadline Extended Reason: Hello designerThank you all very much for your hard work on our project. Im sorry but i need to extend the date of my project. Our parent conpany Rook Nine Prodactions sponsors Bay Youth Assemblies and we are currently at their leadership conference on the Cape. I will be back in on Monday and with your help will get this finished by Thursday the 16th. Thanks Added Thursday, March 9, 2017

Project Deadline Extended Reason: One of the designers is not responding so I now have to make revisions with other designers. I hope to get this website done over the weekends so please get your revisions as soon as possible. Thank you. I am also upgrading the budget another $75 to hopefully get some more interest on my project. Added Wednesday, March 15, 2017

Target Market(s)

Wedding - Corporate -

Industry/Entity Type

It Company

Coding

Coded - Design and coding required

Number of Pages Required

5+ page

Font styles to use
Sans Serif

Requirements
Must have
• Photo Gallery - I want to be able to edit it myself
Nice to have
• I like the look of my friends website brightvaleevents.example

```html
<!DOCTYPE html>
<html lang="en">
<head>
<meta charset="utf-8">
<title>Maple Lantern Productions</title>
<link rel="stylesheet" href="https://fonts.googleapis.com/css2?family=Roboto:wght@300;400;500;700&family=Dancing+Script:wght@600&display=swap">
<style>
:root{
  --orange:#f26b22;
  --orange-light:#f7833a;
  --orange-deep:#d9531a;
  --black:#111111;
  --ink:#222222;
  --grey-text:#666666;
  --grey-panel:#f2f2f2;
  --footer:#333333;
  --white:#ffffff;
}
*{box-sizing:border-box;margin:0;padding:0}
html,body{width:1200px;height:3371px;overflow:hidden}
body{position:relative;font-family:"Roboto",sans-serif;color:var(--ink);background:var(--white)}
.abs{position:absolute}

/* header */
.site-header{position:absolute;left:0;top:0;width:1200px;height:124px;background:var(--white);z-index:2}
.brand{position:absolute;left:70px;top:16px;width:166px;text-align:center}
.brand-mark{width:54px;height:54px;border-radius:50%;background:var(--orange);margin:0 auto 6px}
.brand-name{font-weight:700;font-size:17px;line-height:19px;color:var(--black);text-transform:uppercase;letter-spacing:.3px}
.social-top{position:absolute;right:76px;top:14px;display:flex;gap:17px}
.social-top span{width:40px;height:40px;border-radius:50%;background:#2f5fa8}
.social-top span:nth-child(2){background:#1da1f2}
.social-top span:nth-child(3){background:#dd4b39}
.social-top span:nth-child(4){background:#0e76a8}
.main-nav{position:absolute;right:76px;top:76px;display:flex;gap:31px;font-size:16px;text-transform:uppercase;color:var(--ink)}

/* hero */
.hero{position:absolute;left:0;top:124px;width:1200px;height:573px;
  background:linear-gradient(180deg,#f4dcec 0%,#e7a9cf 22%,#c783b0 42%,#a4708a 58%,#b0603c 72%,#8a4322 86%,#5a2a16 100%)}
.hero-title{position:absolute;left:0;width:100%;top:430px;text-align:center;font-weight:300;font-size:47px;color:var(--white);letter-spacing:.5px;text-transform:uppercase;text-shadow:0 1px 3px rgba(0,0,0,.35)}
.hero-tagline{position:absolute;left:0;width:100%;top:493px;text-align:center;font-family:"Dancing Script",cursive;font-weight:600;font-size:27px;color:var(--white);text-shadow:0 1px 3px rgba(0,0,0,.4)}
.btn{display:inline-flex;align-items:center;justify-content:center;gap:8px;border-radius:26px;font-size:17px;text-transform:uppercase;font-weight:500}
.btn-white{position:absolute;left:498px;top:553px;width:204px;height:50px;background:var(--white);color:var(--orange)}
.btn-orange{background:var(--orange);color:var(--white)}
.btn-black{background:var(--black);color:var(--white)}

/* headings */
.section-title{position:absolute;left:0;width:1200px;text-align:center;font-weight:400;font-size:40px;text-transform:uppercase}
.section-title em{font-style:normal;color:var(--orange)}
.on-orange{color:var(--white)}
.lead{position:absolute;left:124px;width:952px;text-align:center;font-size:15.5px;line-height:25px;color:var(--grey-text)}

/* services */
.band{position:absolute;left:0;width:1200px;background:linear-gradient(135deg,#de5518 0%,#f38a3e 35%,#f07a30 55%,#e2621f 75%,#c94c14 100%)}
.service-card{position:absolute;top:1182px;width:321px;height:372px}
.service-photo{width:321px;height:182px}
.service-body{position:absolute;left:14px;top:182px;width:293px;height:164px;background:var(--white);text-align:center}
.service-body h3{font-weight:400;font-size:25px;color:var(--orange);margin-top:10px}
.service-body p{font-size:15px;line-height:27px;color:var(--grey-text);margin-top:2px;padding:0 18px}
.service-card .btn{position:absolute;left:74px;top:321px;width:173px;height:50px}

/* about */
.member{position:absolute;top:1843px;width:496px;height:241px;background:var(--grey-panel);border-bottom:3px solid var(--orange)}
.member-frame{position:absolute;top:1847px;width:10px;height:241px;border-left:1px solid var(--orange);border-bottom:1px solid var(--orange)}
.member-photo{position:absolute;left:8px;top:0;width:207px;height:238px;background:linear-gradient(180deg,#9a9590 0%,#5c5650 45%,#2b2623 100%)}
.member-photo svg{position:absolute;left:89px;top:101px}
.member-info{position:absolute;left:236px;top:18px}
.member-info h4{font-weight:400;font-size:22px;color:var(--orange)}
.member-info .role{font-size:14px;color:var(--grey-text);margin-top:4px}
.member-social{display:flex;gap:12px;margin:14px 0 10px}
.member-social span{width:30px;height:30px;border-radius:50%;border:1px solid #999;display:flex;align-items:center;justify-content:center}
.contact-line{display:flex;align-items:center;gap:14px;font-size:15px;height:32px;color:var(--ink)}
.contact-line.mail{color:var(--grey-text)}

/* events */
.event-card{position:absolute;top:2362px;width:321px;height:368px;background:var(--black);color:var(--white)}
.event-photo{width:321px;height:188px}
.event-meta{display:flex;justify-content:space-between;align-items:center;padding:0 18px;margin-top:16px;font-size:15px}
.event-meta span{display:flex;align-items:center;gap:8px}
.event-card h4{font-weight:400;font-size:22px;padding:0 22px;margin-top:14px}
.event-card p{font-size:15px;line-height:27px;padding:0 34px 0 22px;margin-top:12px}
.event-card p u{margin-left:6px}

/* gallery */
.gallery-tile{position:absolute;top:2924px;width:233px;height:139px}
.gallery-tile .frame{position:absolute;left:17px;top:17px;right:17px;bottom:17px;border:1px solid rgba(255,255,255,.8);display:flex;align-items:center;justify-content:center;color:var(--white);font-size:19px}
.g-arrow{position:absolute;top:2973px;width:40px;height:40px;display:flex;align-items:center;justify-content:center}

/* footer */
.site-footer{position:absolute;left:0;top:3117px;width:1200px;height:200px;background:var(--footer);color:var(--white)}
.footer-nav{position:absolute;left:79px;top:22px;display:flex;gap:30px;font-size:15px}
.footer-social{position:absolute;right:88px;top:24px;display:flex;gap:20px}
.footer-social span{width:16px;height:16px;border-radius:50%;background:var(--white)}
.footer-rule{position:absolute;left:79px;top:69px;width:1042px;height:1px;background:#5a5a5a}
.footer-title{position:absolute;left:84px;top:86px;font-size:22px;font-weight:400}
.footer-item{position:absolute;top:120px;display:flex;align-items:center;gap:16px;font-size:15px;line-height:22px}
.footer-item .ico{width:40px;height:40px;border-radius:50%;background:var(--white);display:flex;align-items:center;justify-content:center;flex:none}
.footer-item .ico.orange{background:var(--orange)}
.copyright{position:absolute;left:0;top:3317px;width:1200px;height:54px;background:var(--orange);color:var(--white);text-align:center;line-height:54px;font-size:15px}
.copyright b{font-weight:700;text-transform:uppercase}
</style>
</head>
<body>

<header class="site-header">
  <div class="brand">
    <div class="brand-mark"></div>
    <div class="brand-name">Maple Lantern<br>Productions</div>
  </div>
  <div class="social-top"><span></span><span></span><span></span><span></span></div>
  <nav class="main-nav">
    <span>Home</span><span>About</span><span>Services</span><span>My Events</span><span>Testimonials</span><span>Gallery</span><span>Contact Us</span>
  </nav>
</header>

<section class="hero" role="img" aria-label="Wedding reception hall with draped ceiling fabric, chandelier, warm pink uplighting and a wooden dance floor"></section>
<h1 class="hero-title">Maple Lantern Productions</h1>
<p class="hero-tagline">We provides sound, lighting, and Audio Visual services.</p>
<a class="btn btn-white">Contact Us Now</a>

<!-- welcome -->
<h2 class="section-title" style="top:744px">Welcome to <em>Maple Lantern Productions</em></h2>
<p class="lead" style="top:812px">Lorem Ipsum is simply dummy text of the printing and typesetting industry. Lorem Ipsum has been the industry's standard dummy text ever since the 1500s, when an unknown printer took a galley of type and scrambled it to make a type specimen book. It has survived not only five centuries, but also the leap into electronic typesetting, remaining essentially unchanged. It was popularised in the 1960s with the release of Letraset sheets containing Lorem Ipsum passages.</p>
<a class="btn btn-orange abs" style="left:514px;top:940px;width:172px;height:50px">Read More
  <svg width="12" height="12" viewBox="0 0 12 12"><path d="M1 1l4 5-4 5M6 1l4 5-4 5" fill="none" stroke="#fff" stroke-width="1.8"/></svg></a>

<!-- services -->
<section class="band" style="top:1040px;height:564px" role="img" aria-label="Concert crowd under orange stage lights"></section>
<h2 class="section-title on-orange" style="top:1088px">Our Services</h2>

<div class="service-card" style="left:79px">
  <div class="service-photo" role="img" aria-label="Singer performing on stage in front of green and purple lights" style="background:linear-gradient(135deg,#14a07a 0%,#2a6a8a 30%,#7a2ab0 60%,#1a0f30 100%)"></div>
  <div class="service-body"><h3>Sound</h3><p>Lorem Ipsum is simply dummy text of the printing and typesetting industry. Lorem Ipsum has been the industry's.</p></div>
  <a class="btn btn-black">Read More <svg width="12" height="12" viewBox="0 0 12 12"><path d="M1 1l4 5-4 5M6 1l4 5-4 5" fill="none" stroke="#fff" stroke-width="1.8"/></svg></a>
</div>
<div class="service-card" style="left:439px">
  <div class="service-photo" role="img" aria-label="Reception tent with draped fabric, chandelier and pink lighting" style="background:linear-gradient(180deg,#f6e0ec 0%,#e2a2cc 40%,#c47aa8 70%,#8b5a78 100%)"></div>
  <div class="service-body"><h3>Lighting</h3><p>Lorem Ipsum is simply dummy text of the printing and typesetting industry. Lorem Ipsum has been the industry's.</p></div>
  <a class="btn btn-black">Read More <svg width="12" height="12" viewBox="0 0 12 12"><path d="M1 1l4 5-4 5M6 1l4 5-4 5" fill="none" stroke="#fff" stroke-width="1.8"/></svg></a>
</div>
<div class="service-card" style="left:800px">
  <div class="service-photo" role="img" aria-label="Video camera recording an event" style="background:linear-gradient(135deg,#e6e0da 0%,#9a918a 35%,#4a4440 65%,#1e1a18 100%)"></div>
  <div class="service-body"><h3>Audio Visual</h3><p>Lorem Ipsum is simply dummy text of the printing and typesetting industry. Lorem Ipsum has been the industry's.</p></div>
  <a class="btn btn-black">Read More <svg width="12" height="12" viewBox="0 0 12 12"><path d="M1 1l4 5-4 5M6 1l4 5-4 5" fill="none" stroke="#fff" stroke-width="1.8"/></svg></a>
</div>

<!-- about -->
<h2 class="section-title" style="top:1651px">About <em>Us</em></h2>
<p class="lead" style="top:1708px">Lorem Ipsum is simply dummy text of the printing and typesetting industry. Lorem Ipsum has been the industry's standard dummy text ever since the 1500s, when an unknown printer took a galley of type and scrambled it to make a type specimen book. It has survived not only five centuries, but also the leap into electronic typesetting, remaining essentially unchanged.</p>

<div class="member-frame" style="left:76px"></div>
<div class="member" style="left:79px">
  <div class="member-photo" role="img" aria-label="Portrait of a team member">
    <svg width="28" height="28" viewBox="0 0 28 28"><path d="M14 2v24M2 14h24" stroke="#fff" stroke-width="5"/></svg>
  </div>
  <div class="member-info">
    <h4>Member Name</h4>
    <div class="role">Event Organizer</div>
    <div class="member-social"><span></span><span></span><span></span>
      <span><svg width="14" height="10" viewBox="0 0 14 10"><rect x=".5" y=".5" width="13" height="9" fill="none" stroke="#777"/><path d="M.5 .5l6.5 5 6.5-5" fill="none" stroke="#777"/></svg></span></div>
    <div class="contact-line"><svg width="18" height="18" viewBox="0 0 24 24"><path d="M6.6 10.8a15 15 0 006.6 6.6l2.2-2.2a1 1 0 011-.25 11 11 0 003.5.56 1 1 0 011 1V20a1 1 0 01-1 1A17 17 0 013 4a1 1 0 011-1h3.5a1 1 0 011 1 11 11 0 00.56 3.5 1 1 0 01-.25 1z" fill="#f26b22"/></svg>123 456 7890</div>
    <div class="contact-line"><svg width="18" height="18" viewBox="0 0 18 18"><rect x="3" y="1" width="12" height="6" fill="none" stroke="#f26b22" stroke-width="2"/><rect x="1" y="7" width="16" height="10" rx="2" fill="#f26b22"/><rect x="5" y="10" width="8" height="4" fill="#fff"/></svg>123 456 7890</div>
    <div class="contact-line mail"><svg width="18" height="14" viewBox="0 0 18 14"><rect x="1" y="1" width="16" height="12" fill="none" stroke="#f26b22" stroke-width="1.6"/><path d="M1 1l8 7 8-7" fill="none" stroke="#f26b22" stroke-width="1.6"/></svg>info@maplelantern.example</div>
  </div>
</div>

<div class="member-frame" style="left:628px"></div>
<div class="member" style="left:631px">
  <div class="member-photo" role="img" aria-label="Portrait of a team member">
    <svg width="28" height="28" viewBox="0 0 28 28"><path d="M14 2v24M2 14h24" stroke="#fff" stroke-width="5"/></svg>
  </div>
  <div class="member-info">
    <h4>Member Name</h4>
    <div class="role">Event Organizer</div>
    <div class="member-social"><span></span><span></span><span></span>
      <span><svg width="14" height="10" viewBox="0 0 14 10"><rect x=".5" y=".5" width="13" height="9" fill="none" stroke="#777"/><path d="M.5 .5l6.5 5 6.5-5" fill="none" stroke="#777"/></svg></span></div>
    <div class="contact-line"><svg width="18" height="18" viewBox="0 0 24 24"><path d="M6.6 10.8a15 15 0 006.6 6.6l2.2-2.2a1 1 0 011-.25 11 11 0 003.5.56 1 1 0 011 1V20a1 1 0 01-1 1A17 17 0 013 4a1 1 0 011-1h3.5a1 1 0 011 1 11 11 0 00.56 3.5 1 1 0 01-.25 1z" fill="#f26b22"/></svg>123 456 7890</div>
    <div class="contact-line"><svg width="18" height="18" viewBox="0 0 18 18"><rect x="3" y="1" width="12" height="6" fill="none" stroke="#f26b22" stroke-width="2"/><rect x="1" y="7" width="16" height="10" rx="2" fill="#f26b22"/><rect x="5" y="10" width="8" height="4" fill="#fff"/></svg>123 456 7890</div>
    <div class="contact-line mail"><svg width="18" height="14" viewBox="0 0 18 14"><rect x="1" y="1" width="16" height="12" fill="none" stroke="#f26b22" stroke-width="1.6"/><path d="M1 1l8 7 8-7" fill="none" stroke="#f26b22" stroke-width="1.6"/></svg>info@maplelantern.example</div>
  </div>
</div>

<a class="btn btn-orange abs" style="left:502px;top:2121px;width:196px;height:50px">Meet With Us
  <svg width="12" height="12" viewBox="0 0 12 12"><path d="M1 1l4 5-4 5M6 1l4 5-4 5" fill="none" stroke="#fff" stroke-width="1.8"/></svg></a>

<!-- events -->
<section class="band" style="top:2224px;height:558px" role="img" aria-label="Guests celebrating at a party, tinted orange"></section>
<h2 class="section-title on-orange" style="top:2267px">My Events</h2>

<div class="event-card" style="left:79px">
  <div class="event-photo" role="img" aria-label="Couple dancing at a wedding under purple lights" style="background:linear-gradient(135deg,#2a1a8a 0%,#5a3ac0 35%,#9a6ae0 55%,#3a2090 80%,#1a1050 100%)"></div>
  <div class="event-meta">25 Feb 2017<span><svg width="18" height="16" viewBox="0 0 18 16"><path d="M2 2h10v7H6l-3 3V9H2z" fill="none" stroke="#fff" stroke-width="1.5"/><path d="M13 5h3v7h-1v2l-2-2H8" fill="none" stroke="#fff" stroke-width="1.5"/></svg>2 comments</span></div>
  <h4>Event Title</h4>
  <p>Lorem Ipsum is simply dummy text of the printing and typesetting industry. Lorem Ipsum has the...<u>READ MORE</u></p>
</div>
<div class="event-card" style="left:439px">
  <div class="event-photo" role="img" aria-label="Close view of a lit sound mixing desk" style="background:linear-gradient(135deg,#1a3a8a 0%,#3a5ab0 25%,#f08a30 50%,#c04a2a 75%,#2a1a3a 100%)"></div>
  <div class="event-meta">25 Feb 2017<span><svg width="18" height="16" viewBox="0 0 18 16"><path d="M2 2h10v7H6l-3 3V9H2z" fill="none" stroke="#fff" stroke-width="1.5"/><path d="M13 5h3v7h-1v2l-2-2H8" fill="none" stroke="#fff" stroke-width="1.5"/></svg>2 comments</span></div>
  <h4>Event Title</h4>
  <p>Lorem Ipsum is simply dummy text of the printing and typesetting industry. Lorem Ipsum has the...<u>READ MORE</u></p>
</div>
<div class="event-card" style="left:800px">
  <div class="event-photo" role="img" aria-label="Banquet hall with blue draped lighting" style="background:linear-gradient(180deg,#6a9af0 0%,#3a6ad8 35%,#1a3aa0 70%,#0a1850 100%)"></div>
  <div class="event-meta">25 Feb 2017<span><svg width="18" height="16" viewBox="0 0 18 16"><path d="M2 2h10v7H6l-3 3V9H2z" fill="none" stroke="#fff" stroke-width="1.5"/><path d="M13 5h3v7h-1v2l-2-2H8" fill="none" stroke="#fff" stroke-width="1.5"/></svg>2 comments</span></div>
  <h4>Event Title</h4>
  <p>Lorem Ipsum is simply dummy text of the printing and typesetting industry. Lorem Ipsum has the...<u>READ MORE</u></p>
</div>

<!-- gallery -->
<h2 class="section-title" style="top:2829px"><em>Gallery</em></h2>
<div class="g-arrow" style="left:27px;background:var(--black)"><svg width="12" height="20" viewBox="0 0 12 20"><path d="M10 2L2 10l8 8" fill="none" stroke="#fff" stroke-width="2"/></svg></div>
<div class="gallery-tile" style="left:79px" role="img" aria-label="Wedding guests"><div class="abs" style="inset:0;background:linear-gradient(135deg,#8a7466,#4a3a32 55%,#241c18)"></div><div class="frame">Wedding</div></div>
<div class="gallery-tile" style="left:350px" role="img" aria-label="Corporate event"><div class="abs" style="inset:0;background:linear-gradient(135deg,#6a625c,#3a3430 55%,#1a1614)"></div><div class="frame">Corporate</div></div>
<div class="gallery-tile" style="left:620px" role="img" aria-label="Wedding reception"><div class="abs" style="inset:0;background:linear-gradient(135deg,#9a948e,#5a5652 55%,#2a2826)"></div><div class="frame">Wedding</div></div>
<div class="gallery-tile" style="left:890px" role="img" aria-label="Corporate party"><div class="abs" style="inset:0;background:linear-gradient(135deg,#7a5a46,#44302a 55%,#1e1412)"></div><div class="frame">Corporate</div></div>
<div class="g-arrow" style="left:1133px;background:var(--orange)"><svg width="12" height="20" viewBox="0 0 12 20"><path d="M2 2l8 8-8 8" fill="none" stroke="#fff" stroke-width="2"/></svg></div>

<!-- footer -->
<footer class="site-footer">
  <nav class="footer-nav"><span>Home</span><span>About</span><span>Services</span><span>My Events</span><span>Testimonials</span><span>Gallery</span><span>Contact Us</span></nav>
  <div class="footer-social"><span></span><span></span><span></span></div>
  <div class="footer-rule"></div>
  <h3 class="footer-title">Contact Us</h3>
  <div class="footer-item" style="left:79px">
    <span class="ico orange"><svg width="16" height="20" viewBox="0 0 16 20"><path d="M8 0a7 7 0 017 7c0 5-7 13-7 13S1 12 1 7a7 7 0 017-7z" fill="#fff"/><circle cx="8" cy="7" r="2.6" fill="#f26b22"/></svg></span>
    <span>123 Building name,<br>Street Name,Country</span>
  </div>
  <div class="footer-item" style="left:348px">
    <span class="ico"><svg width="20" height="20" viewBox="0 0 24 24"><path d="M6.6 10.8a15 15 0 006.6 6.6l2.2-2.2a1 1 0 011-.25 11 11 0 003.5.56 1 1 0 011 1V20a1 1 0 01-1 1A17 17 0 013 4a1 1 0 011-1h3.5a1 1 0 011 1 11 11 0 00.56 3.5 1 1 0 01-.25 1z" fill="#f26b22"/></svg></span>
    <span>123 456 7890</span>
  </div>
  <div class="footer-item" style="left:622px">
    <span class="ico"><svg width="18" height="18" viewBox="0 0 18 18"><rect x="3" y="1" width="12" height="6" fill="none" stroke="#f26b22" stroke-width="2"/><rect x="1" y="7" width="16" height="10" rx="2" fill="#f26b22"/><rect x="5" y="10" width="8" height="4" fill="#fff"/></svg></span>
    <span>123 456 7890</span>
  </div>
  <div class="footer-item" style="left:892px">
    <span class="ico"><svg width="18" height="14" viewBox="0 0 18 14"><rect x="1" y="1" width="16" height="12" fill="none" stroke="#f26b22" stroke-width="1.8"/><path d="M1 1l8 7 8-7" fill="none" stroke="#f26b22" stroke-width="1.8"/></svg></span>
    <span>info@maplelantern.example</span>
  </div>
</footer>
<div class="copyright">© <b>Maple Lantern Productions - 2017.</b>&nbsp; All Rights Reserved.</div>

</body>
</html>
```